New Business Card Design Project

We require a business card design for Vexalund, a newly established Indian company.
Our focus is on the development, manufacturing, and export of a diverse array of pharmaceutical products on a global scale. The card should convey a professional appearance, as our primary markets are in Africa, China, and Southeast Asian nations.
We envision a two-sided business card, with the reverse side dedicated to a logo set against a solid color or an elegantly designed pattern. The corners should be rounded. We would appreciate seeing both horizontal and vertical design options. We trust the designer to utilize their expertise in creating this design.

The content for the business card is included in the attached Word file.

Target Market(s)

Our primary markets are in Africa, China, and Southeast Asian, Latin America, Maldives, Sri Lanka

Industry/Entity Type

Pharmaceutical Manufacturing and Export

Contact Information for Business Card

Colors

Designer to choose colors to be used in the design.

Requirements
Must have
• The reverse side of the business card features solely the logo along with the tagline, "Care Across Borders."
Should not have
• The logo should not exceed two instances, encompassing both the front and back sides of the card.

```html
<!DOCTYPE html>
<html lang="en">
<head>
<meta charset="utf-8">
<title>Vexalund Business Card</title>
<link rel="stylesheet" href="https://fonts.googleapis.com/css2?family=Montserrat:wght@400;700;800&family=Open+Sans:wght@400;600&display=swap">
<style>
  :root {
    --stage: #222222;
    --card: #1c1c1c;
    --blue: #2ea8e0;
    --coral: #f2634d;
    --white: #ffffff;
  }
  * { box-sizing: border-box; margin: 0; padding: 0; }
  html, body { width: 1200px; height: 711px; overflow: hidden; }
  body {
    background: var(--stage);
    font-family: "Open Sans", sans-serif;
    display: flex;
    align-items: center;
    justify-content: center;
    gap: 40px;
  }
  .card {
    position: relative;
    width: 540px;
    height: 309px;
    background: var(--card);
    border-radius: 22px;
    border-bottom: 4px solid var(--blue);
    border-left: 3px solid var(--blue);
    overflow: hidden;
  }
  /* Back side */
  .card-back {
    display: flex;
    flex-direction: column;
    align-items: center;
    justify-content: center;
  }
  .brand {
    display: flex;
    align-items: center;
    gap: 10px;
    font-family: "Montserrat", sans-serif;
    font-weight: 800;
    color: var(--blue);
    letter-spacing: 0.5px;
  }
  .brand-dot {
    border-radius: 50%;
    background: var(--coral);
    flex: none;
  }
  .card-back .brand { font-size: 58px; }
  .card-back .brand-dot { width: 18px; height: 18px; }
  .tagline {
    margin-top: 10px;
    font-family: "Montserrat", sans-serif;
    font-size: 13px;
    color: var(--white);
    letter-spacing: 0.6px;
  }
  /* Front side */
  .front-art { position: absolute; inset: 0; }
  .holder {
    position: absolute;
    top: 22px;
    right: 34px;
    text-align: right;
    font-family: "Montserrat", sans-serif;
  }
  .holder-name { font-size: 22px; color: var(--blue); font-weight: 400; }
  .holder-name strong { font-weight: 800; }
  .holder-role { font-size: 12px; color: var(--white); margin-top: 2px; }
  .accent-bar {
    position: absolute;
    top: 22px; right: 0;
    width: 18px; height: 48px;
    background: var(--blue);
  }
  .card-front .brand {
    position: absolute;
    top: 92px; left: 40px;
    font-size: 40px;
  }
  .card-front .brand-dot { width: 13px; height: 13px; }
  .contact {
    position: absolute;
    top: 170px; left: 40px;
    list-style: none;
    font-size: 13px;
    color: var(--white);
  }
  .contact li { display: flex; align-items: center; gap: 10px; line-height: 22px; }
  .contact svg { width: 14px; height: 14px; flex: none; }
  .address {
    position: absolute;
    right: 30px; bottom: 40px;
    text-align: right;
    font-size: 13px;
    line-height: 19px;
    color: var(--white);
  }
</style>
</head>
<body>
  <section class="card card-back" aria-label="Card back">
    <div class="brand"><span class="brand-dot"></span>Vexalund</div>
    <p class="tagline">Care Across Borders.</p>
  </section>

  <section class="card card-front" aria-label="Card front">
    <svg class="front-art" viewBox="0 0 540 309" preserveAspectRatio="none" aria-hidden="true">
      <path d="M0,262 C120,292 240,272 330,205" fill="none" stroke="var(--coral)" stroke-width="7"/>
      <path d="M0,284 C150,300 270,262 335,170 C375,112 420,92 540,86 L540,309 L0,309 Z" fill="var(--blue)"/>
    </svg>
    <span class="accent-bar"></span>
    <div class="holder">
      <p class="holder-name"><strong>Rohan</strong> K. Batra</p>
      <p class="holder-role">CEO</p>
    </div>
    <div class="brand"><span class="brand-dot"></span>Vexalund</div>
    <ul class="contact">
      <li>
        <svg viewBox="0 0 14 14"><rect x="3" y="1" width="8" height="12" rx="1.5" fill="none" stroke="var(--coral)" stroke-width="1.5"/></svg>
        +919 421350170
      </li>
      <li>
        <svg viewBox="0 0 14 14"><circle cx="7" cy="7" r="5.8" fill="none" stroke="var(--blue)" stroke-width="1.4"/><path d="M1.5,7 H12.5 M7,1.2 C4,4 4,10 7,12.8 M7,1.2 C10,4 10,10 7,12.8" fill="none" stroke="var(--blue)" stroke-width="1"/></svg>
        www.vexalund.com
      </li>
      <li>
        <svg viewBox="0 0 14 14"><rect x="1" y="3" width="12" height="9" rx="1" fill="none" stroke="var(--coral)" stroke-width="1.4"/><path d="M1.5,3.5 L7,8 L12.5,3.5" fill="none" stroke="var(--coral)" stroke-width="1.2"/></svg>
        rbatra@vexalund.com
      </li>
    </ul>
    <p class="address">12, Sunrise Colony,<br>Nagpur, 440010, India</p>
  </section>
</body>
</html>
```